Can design for new all natural low calorie spiked lemonade

We need a clean but catchy can design for a new spiked lemonade that will be all natural, gluten free and low in calories. Open to any creative ideas ranging from designs such as using a lemonade stand to simple designs such as the example pictures that are uploaded. Looking for a can that just pops out right away on the shelf but also believe less is more as far as simplicity. The beverage is called Brightwell Spiked Lemonade, that features 3 flavors. Traditional Lemonade, Peach Lemonade and lastly Strawberry Lemonade.

Target Market(s)

21-55 years of age. 75% female, 25% male.

Colors

Designer to choose colors to be used in the design.

Requirements
Must have
• The brand name is Brightwell and it is a spiked lemonade so that should be catchy so the consumer knows what it is on first glance. Must say gluten free, all natural, and 150 calories on the front of the can. Would like some type of image on the front middle of the can. There are 3 flavors so the can should blend well with each fruit but not be different cans

```html
<!DOCTYPE html>
<html lang="en">
<head>
<meta charset="utf-8">
<title>Brightwell Spiked Lemonade – Can Range</title>
<link href="https://fonts.googleapis.com/css2?family=Open+Sans:wght@600;700&family=Oswald:wght@400&display=swap" rel="stylesheet">
<style>
  :root {
    --backdrop: #74b2bb;
    --label-cream: #f1efe9;
    --brand-green: #7aa62c;
    --badge-green: #86b02f;
    --ink: #333333;
    --rim: #d9dcdd;
    --peach: #f29a8a;
    --peach-text: #ee9a88;
    --lemon: #f5b82e;
    --lemon-text: #8db43a;
    --berry: #f2557a;
    --berry-text: #d83a55;
    --white: #ffffff;
  }
  * { margin: 0; padding: 0; box-sizing: border-box; }
  html, body { width: 1200px; height: 705px; overflow: hidden; }
  body { background: var(--backdrop); font-family: "Open Sans", sans-serif; }

  .range { position: relative; width: 1200px; height: 705px; }

  .can {
    position: absolute; top: 128px; width: 212px; height: 520px;
    --flavour: var(--peach);
  }
  .can--peach { left: 198px; --flavour: var(--peach); --flavour-text: var(--peach-text); }
  .can--lemon { left: 500px; --flavour: var(--lemon); --flavour-text: var(--lemon-text); }
  .can--berry { left: 780px; --flavour: var(--berry); --flavour-text: var(--berry-text); }

  .can__lid {
    position: absolute; left: 20px; right: 20px; top: 0; height: 8px;
    background: var(--rim); border-radius: 4px 4px 0 0;
  }
  .can__shoulder {
    position: absolute; left: 0; right: 0; top: 8px; height: 44px;
    background: var(--flavour); clip-path: polygon(8% 0, 92% 0, 100% 100%, 0 100%);
  }
  .can__body {
    position: absolute; left: 0; right: 0; top: 52px; height: 332px;
    background: var(--label-cream);
  }
  .can__stripes {
    position: absolute; left: 0; right: 0; top: 384px; height: 112px;
    background:
      linear-gradient(var(--white), var(--white)) 0 20px / 100% 4px no-repeat,
      linear-gradient(var(--white), var(--white)) 0 40px / 100% 4px no-repeat,
      linear-gradient(var(--white), var(--white)) 0 68px / 100% 4px no-repeat,
      linear-gradient(var(--white), var(--white)) 0 88px / 100% 4px no-repeat,
      var(--flavour);
  }
  .can__base {
    position: absolute; left: 14px; right: 14px; top: 496px; height: 24px;
    background: var(--rim); clip-path: polygon(0 0, 100% 0, 94% 100%, 6% 100%);
  }

  .brand {
    position: absolute; left: 0; right: 0; top: 104px; text-align: center;
    font-family: "Open Sans", sans-serif; font-weight: 700; font-size: 27px;
    color: var(--brand-green); line-height: 1;
  }
  .product-type {
    position: absolute; left: 0; right: 0; top: 145px; text-align: center;
    font-weight: 700; font-size: 14.5px; letter-spacing: 0.3px; color: var(--ink);
  }
  .fruit {
    position: absolute; left: 26px; right: 26px; top: 190px; height: 150px;
    border-radius: 40%;
  }
  .can--peach .fruit { background: radial-gradient(circle, #f4a77a 0%, #f6c392 55%, var(--label-cream) 78%); }
  .can--lemon .fruit { background: radial-gradient(circle, #f7d232 0%, #f5e27a 55%, var(--label-cream) 78%); }
  .can--berry .fruit { background: radial-gradient(circle, #d8263a 0%, #e86a6a 50%, #9cc06a 62%, var(--label-cream) 80%); }

  .flavour-name {
    position: absolute; left: 0; right: 0; top: 352px; text-align: center;
    font-weight: 700; font-size: 19px; letter-spacing: 0.5px; color: var(--flavour-text);
  }

  .claims {
    position: absolute; left: 0; right: 0; top: 413px; height: 48px;
    display: flex; align-items: center; justify-content: center; gap: 8px;
  }
  .claim {
    font-family: "Oswald", sans-serif; font-size: 12.5px; color: var(--white);
    letter-spacing: 0.2px; width: 72px;
  }
  .claim--left { text-align: right; }
  .claim--right { text-align: left; }
  .calories {
    width: 48px; height: 48px; border-radius: 50%;
    background: var(--badge-green); border: 3px solid var(--white);
    display: flex; flex-direction: column; align-items: center; justify-content: center;
    color: var(--white); line-height: 1;
  }
  .calories__value { font-weight: 700; font-size: 16px; }
  .calories__unit { font-weight: 600; font-size: 5px; letter-spacing: 0.3px; margin-top: 1px; }
</style>
</head>
<body>
<main class="range">

  <article class="can can--peach">
    <div class="can__lid"></div>
    <div class="can__shoulder"></div>
    <div class="can__body"></div>
    <div class="can__stripes"></div>
    <div class="can__base"></div>
    <h2 class="brand">Brightwell</h2>
    <p class="product-type">SPIKED LEMONADE</p>
    <div class="fruit" role="img" aria-label="Photo of whole and sliced peaches with leaves and scattered dots"></div>
    <p class="flavour-name">Peach</p>
    <div class="claims">
      <span class="claim claim--left">GLUTEN FREE</span>
      <div class="calories"><span class="calories__value">150</span><span class="calories__unit">CALORIES</span></div>
      <span class="claim claim--right">ALL NATURAL</span>
    </div>
  </article>

  <article class="can can--lemon">
    <div class="can__lid"></div>
    <div class="can__shoulder"></div>
    <div class="can__body"></div>
    <div class="can__stripes"></div>
    <div class="can__base"></div>
    <h2 class="brand">Brightwell</h2>
    <p class="product-type">SPIKED LEMONADE</p>
    <div class="fruit" role="img" aria-label="Photo of whole and halved lemons with leaves and scattered dots"></div>
    <p class="flavour-name">Lemonade</p>
    <div class="claims">
      <span class="claim claim--left">GLUTEN FREE</span>
      <div class="calories"><span class="calories__value">150</span><span class="calories__unit">CALORIES</span></div>
      <span class="claim claim--right">ALL NATURAL</span>
    </div>
  </article>

  <article class="can can--berry">
    <div class="can__lid"></div>
    <div class="can__shoulder"></div>
    <div class="can__body"></div>
    <div class="can__stripes"></div>
    <div class="can__base"></div>
    <h2 class="brand">Brightwell</h2>
    <p class="product-type">SPIKED LEMONADE</p>
    <div class="fruit" role="img" aria-label="Photo of fresh strawberries with leaves and scattered dots"></div>
    <p class="flavour-name">Strawberry</p>
    <div class="claims">
      <span class="claim claim--left">GLUTEN FREE</span>
      <div class="calories"><span class="calories__value">150</span><span class="calories__unit">CALORIES</span></div>
      <span class="claim claim--right">ALL NATURAL</span>
    </div>
  </article>

</main>
</body>
</html>
```